Podcast cover that can bring to live the topic of talent analytics which is both an art and science.

To design a podcast cover that must:
- clearly indicate the title of the podcast “Crewmark Signals Weekly”
- reflects the art and science of analytics
- visually communicates how this topic can deliver insights and help decision making by connecting the letters of the podcast title, and/or meshes it with other relevant graphics
- no specific colour palette is required, but the overall design will need to stand out when compared side by side with other podcast covers

Target Market(s)

Business and HR professionals

Industry/Entity Type

Human Resource

Font styles to use
Sans Serif

Colors

Designer to choose colors to be used in the design.

Requirements
Must have
• See project description above
Nice to have
• Data visualisation abstract art to draw interest and reflect the complexity of big data used for talent analytics
Should not have
• Pls do not use icons of people or stick figures in design

```html
<!DOCTYPE html>
<html lang="en">
<head>
<meta charset="utf-8">
<title>Crewmark Signals Weekly – Podcast Cover</title>
<link rel="stylesheet" href="https://fonts.googleapis.com/css2?family=Shrikhand&display=swap">
<style>
  :root {
    --green: #5cff6a;
    --cyan: #5ff0d8;
    --violet: #c98cf5;
    --pink: #ff8fb0;
    --orange: #ffad3a;
    --splash-purple: #8a4fb8;
    --splash-gold: #b89a1c;
    --type-face: #ececec;
    --type-depth: #8d8d8d;
    --chart: #ebebeb;
  }
  html, body {
    margin: 0;
    padding: 0;
    overflow: hidden;
    background: #ffffff;
  }
  .cover {
    position: relative;
    width: 1200px;
    height: 808px;
    overflow: hidden;
    background:
      radial-gradient(ellipse 45% 55% at 8% 52%, var(--green) 0%, rgba(92,255,106,0) 70%),
      radial-gradient(ellipse 45% 40% at 10% 95%, var(--cyan) 0%, rgba(95,240,216,0) 75%),
      radial-gradient(ellipse 40% 50% at 95% 40%, var(--orange) 0%, rgba(255,173,58,0) 75%),
      radial-gradient(ellipse 45% 45% at 70% 30%, var(--pink) 0%, rgba(255,143,176,0) 75%),
      radial-gradient(ellipse 55% 60% at 40% 35%, var(--violet) 0%, rgba(201,140,245,0) 80%),
      linear-gradient(120deg, var(--green) 0%, var(--violet) 45%, var(--pink) 70%, var(--orange) 100%);
  }
  .splash {
    position: absolute;
    top: -40px;
    width: 340px;
    height: 230px;
    border-radius: 0 0 50% 50%;
    opacity: 0.85;
  }
  .splash--left {
    left: -40px;
    background: radial-gradient(ellipse at 40% 20%, var(--splash-purple) 0%, rgba(138,79,184,0.5) 50%, rgba(255,255,255,0) 75%);
  }
  .splash--right {
    right: -40px;
    background: radial-gradient(ellipse at 60% 20%, var(--splash-gold) 0%, rgba(184,154,28,0.5) 50%, rgba(255,255,255,0) 75%);
  }
  .splash--centre {
    left: 500px;
    width: 260px;
    height: 130px;
    background: radial-gradient(ellipse at 50% 10%, rgba(255,255,255,0.9) 0%, rgba(255,255,255,0) 70%);
  }
  .title {
    position: absolute;
    inset: 0;
    margin: 0;
    font-family: "Shrikhand", "Georgia", serif;
    font-weight: 400;
    color: var(--type-face);
    line-height: 1;
  }
  .title span {
    position: absolute;
    white-space: nowrap;
    text-shadow:
      2px 2px 0 var(--type-depth),
      4px 4px 0 var(--type-depth),
      6px 6px 0 var(--type-depth),
      8px 8px 0 var(--type-depth),
      10px 10px 0 var(--type-depth);
  }
  .title__top {
    left: 50%;
    top: 170px;
    transform: translateX(-50%);
    font-size: 108px;
  }
  .title__main {
    left: 50%;
    top: 290px;
    transform: translateX(-50%);
    font-size: 176px;
    letter-spacing: -2px;
  }
  .title__bottom {
    left: 560px;
    top: 460px;
    font-size: 118px;
  }
  .chart {
    position: absolute;
    left: 0;
    bottom: 0;
    width: 1200px;
    height: 220px;
  }
  .chart__bar { fill: var(--chart); }
  .chart__line { fill: none; stroke: var(--chart); stroke-width: 4; }
  .chart__dot { fill: var(--chart); }
</style>
</head>
<body>
  <main class="cover">
    <div class="splash splash--left" role="img" aria-label="Purple paint splash"></div>
    <div class="splash splash--centre" role="img" aria-label="White paint splash"></div>
    <div class="splash splash--right" role="img" aria-label="Gold paint splash"></div>

    <h1 class="title">
      <span class="title__top">Crewmark</span>
      <span class="title__main">Signals</span>
      <span class="title__bottom">Weekly</span>
    </h1>

    <svg class="chart" viewBox="0 588 1200 220" aria-hidden="true">
      <g class="chart__bars">
        <rect class="chart__bar" x="10" y="690" width="30" height="118"/>
        <rect class="chart__bar" x="59" y="720" width="30" height="88"/>
        <rect class="chart__bar" x="108" y="685" width="30" height="123"/>
        <rect class="chart__bar" x="157" y="715" width="30" height="93"/>
        <rect class="chart__bar" x="206" y="690" width="30" height="118"/>
        <rect class="chart__bar" x="255" y="725" width="30" height="83"/>
        <rect class="chart__bar" x="304" y="685" width="30" height="123"/>
        <rect class="chart__bar" x="353" y="715" width="30" height="93"/>
        <rect class="chart__bar" x="402" y="690" width="30" height="118"/>
        <rect class="chart__bar" x="451" y="720" width="30" height="88"/>
        <rect class="chart__bar" x="500" y="680" width="30" height="128"/>
        <rect class="chart__bar" x="549" y="715" width="30" height="93"/>
        <rect class="chart__bar" x="598" y="690" width="30" height="118"/>
        <rect class="chart__bar" x="647" y="725" width="30" height="83"/>
        <rect class="chart__bar" x="696" y="685" width="30" height="123"/>
        <rect class="chart__bar" x="745" y="715" width="30" height="93"/>
        <rect class="chart__bar" x="794" y="690" width="30" height="118"/>
        <rect class="chart__bar" x="843" y="720" width="30" height="88"/>
        <rect class="chart__bar" x="892" y="685" width="30" height="123"/>
        <rect class="chart__bar" x="941" y="715" width="30" height="93"/>
        <rect class="chart__bar" x="990" y="690" width="30" height="118"/>
        <rect class="chart__bar" x="1039" y="725" width="30" height="83"/>
        <rect class="chart__bar" x="1088" y="685" width="30" height="123"/>
        <rect class="chart__bar" x="1137" y="710" width="30" height="98"/>
        <rect class="chart__bar" x="1186" y="690" width="30" height="118"/>
      </g>
      <polyline class="chart__line" points="25,640 74,665 123,632 172,660 221,640 270,668 319,632 368,660 417,640 466,665 515,628 564,660 613,640 662,668 711,632 760,660 809,640 858,665 907,632 956,660 1005,640 1054,668 1103,632 1152,655 1201,640"/>
      <g class="chart__dots">
        <circle class="chart__dot" cx="25" cy="640" r="9"/>
        <circle class="chart__dot" cx="74" cy="665" r="9"/>
        <circle class="chart__dot" cx="123" cy="632" r="9"/>
        <circle class="chart__dot" cx="172" cy="660" r="9"/>
        <circle class="chart__dot" cx="221" cy="640" r="9"/>
        <circle class="chart__dot" cx="270" cy="668" r="9"/>
        <circle class="chart__dot" cx="319" cy="632" r="9"/>
        <circle class="chart__dot" cx="368" cy="660" r="9"/>
        <circle class="chart__dot" cx="417" cy="640" r="9"/>
        <circle class="chart__dot" cx="466" cy="665" r="9"/>
        <circle class="chart__dot" cx="515" cy="628" r="9"/>
        <circle class="chart__dot" cx="564" cy="660" r="9"/>
        <circle class="chart__dot" cx="613" cy="640" r="9"/>
        <circle class="chart__dot" cx="662" cy="668" r="9"/>
        <circle class="chart__dot" cx="711" cy="632" r="9"/>
        <circle class="chart__dot" cx="760" cy="660" r="9"/>
        <circle class="chart__dot" cx="809" cy="640" r="9"/>
        <circle class="chart__dot" cx="858" cy="665" r="9"/>
        <circle class="chart__dot" cx="907" cy="632" r="9"/>
        <circle class="chart__dot" cx="956" cy="660" r="9"/>
        <circle class="chart__dot" cx="1005" cy="640" r="9"/>
        <circle class="chart__dot" cx="1054" cy="668" r="9"/>
        <circle class="chart__dot" cx="1103" cy="632" r="9"/>
        <circle class="chart__dot" cx="1152" cy="655" r="9"/>
      </g>
    </svg>
  </main>
</body>
</html>
```